Every Shelf Set Neatly or ESN Organized needs a business card design. ESN Organized is a professi

We need a business card design that is clean, sharp and conveys a sense of organization. I already have a logo.

Target Market(s)

Families (specifically mothers), small business owners, parents, seniors

Industry/Entity Type

Business

Contact Information for Business Card

My website is www.esnorganized-example.com and my Facebook page is http://www.sociallink-example.com/everyshelfsetneatly. The phone number is 418-552-7094 and I want to be listed as Lorna M. Pelham, Owner

Requirements
Must have
• My logo.

```html
<!DOCTYPE html>
<html lang="en">
<head>
<meta charset="utf-8">
<title>ESN Organized — Business Card</title>
<link rel="stylesheet" href="https://fonts.googleapis.com/css2?family=Open+Sans:wght@400;600&display=swap">
<style>
  :root {
    --stage: #8f8f8f;
    --paper: #eeeff1;
    --brand-blue: #1578c8;
    --ink: #111214;
    --text-gray: #4a4a4a;
  }
  * { margin: 0; padding: 0; box-sizing: border-box; }
  html, body { width: 1105px; height: 1200px; overflow: hidden; }
  body {
    background: var(--stage);
    font-family: "Open Sans", Arial, sans-serif;
    position: relative;
  }
  .card {
    position: absolute;
    left: 120px;
    width: 864px;
    height: 493px;
    overflow: hidden;
  }
  .card-front { top: 70px; background: var(--paper); }
  .card-back { top: 637px; background: var(--brand-blue); }

  .accent-bar {
    position: absolute; left: 0; top: 64px;
    width: 19px; height: 64px;
    background: var(--brand-blue);
  }
  .holder-name {
    position: absolute; left: 59px; top: 58px;
    font-size: 32px; font-weight: 600; color: var(--brand-blue);
  }
  .holder-title {
    position: absolute; left: 63px; top: 102px;
    font-size: 22px; color: var(--ink);
  }
  .contact-list {
    position: absolute; left: 64px; top: 336px;
    list-style: none;
  }
  .contact-item {
    display: flex; align-items: center; gap: 10px;
    height: 32px;
    font-size: 22px; color: var(--text-gray);
  }
  .contact-icon { width: 20px; height: 20px; flex: none; }

  .brand-name {
    position: absolute;
    font-weight: 600;
    letter-spacing: 2px;
    white-space: nowrap;
  }
  .card-front .brand-name {
    left: 470px; top: 392px;
    font-size: 30px; color: var(--brand-blue);
    display: flex; align-items: center; gap: 12px;
  }
  .brand-mark {
    width: 16px; height: 16px; background: var(--brand-blue); display: inline-block;
  }
  .card-back .brand-name {
    left: 64px; top: 66px;
    font-size: 46px; color: var(--ink);
  }
  .back-url {
    position: absolute; left: 66px; top: 132px;
    font-size: 19px; font-style: italic; letter-spacing: 6px;
    color: var(--ink);
  }
  .clip-decoration { position: absolute; left: 456px; top: 0; }
</style>
</head>
<body>
  <section class="card card-front" aria-label="Card front">
    <div class="accent-bar"></div>
    <h1 class="holder-name">Lorna M. Pelham</h1>
    <p class="holder-title">Owner</p>
    <ul class="contact-list">
      <li class="contact-item">
        <svg class="contact-icon" viewBox="0 0 20 20" aria-hidden="true">
          <path d="M4 2 L7 2 L8.5 6 L6.5 7.5 Q8 11.5 12.5 13.5 L14 11.5 L18 13 L18 16 Q17 18 15 18 Q3 16 2 5 Q2 3 4 2 Z" fill="var(--brand-blue)"/>
        </svg>
        <span>418-552-7094</span>
      </li>
      <li class="contact-item">
        <svg class="contact-icon" viewBox="0 0 20 20" aria-hidden="true">
          <circle cx="10" cy="10" r="8.5" fill="var(--brand-blue)"/>
          <path d="M1.5 10 H18.5 M10 1.5 Q5 10 10 18.5 M10 1.5 Q15 10 10 18.5" stroke="var(--paper)" stroke-width="1.2" fill="none"/>
        </svg>
        <span>www.esnorganized-example.com</span>
      </li>
      <li class="contact-item">
        <svg class="contact-icon" viewBox="0 0 20 20" aria-hidden="true">
          <rect x="2" y="2" width="16" height="16" fill="var(--brand-blue)"/>
        </svg>
        <span>everyshelfsetneatly</span>
      </li>
    </ul>
    <div class="brand-name"><span class="brand-mark"></span>ESN Organized</div>
  </section>

  <section class="card card-back" aria-label="Card back">
    <div class="brand-name">ESN Organized</div>
    <p class="back-url">www.esnorganized-example.com</p>
    <svg class="clip-decoration" width="408" height="493" viewBox="0 0 408 493" role="img" aria-label="Large paperclip decoration in black and blue">
      <polygon points="220,0 408,0 408,493 0,493 0,420" fill="var(--ink)"/>
    </svg>
  </section>
</body>
</html>
```